physio rehab flyer for Vela Mend please

Specification:
Flyer is to be trifold from letter size (8.5 x 11)
-----------------------This may help you:--------------------------
I would like the look of :
clean, minimalistic look with mainly blue and green
san serif font
professional
The colors I like are blue (not the blue in the logo enclosed, I want a change, but more like the blue on my website logo) and light green.
This is my website: www.velamendgroup.ca just so you get an idea but it will be totally changed soon to a to be determined design.
I like the blue and green in file "sample 2" (enclosed)
I like the pictures in "sample 2" file enclosed
For inspiration, I like design of this brochure: http://www.brelford.ca/HarlowRehab/PatientsFamilies/Clinics_Tests/DKAP_Service/Documents/Brochure.pdf
Here's how I see the pages layout:
----[location: this should be the cover (outside, right panel of trifold)]-----
Vela Mend Logo
Integrated Injury Rehab
Evidence-based, one-on-one care to make your recovery fast and comfortable
www.velamendgroup.ca
---------------[location: inside, left panel]----------------------------------------
Our team leaders
[portrait here]
Harriet Olsavik, MD, FRCPC, MSC, CIME
Physiatrist
Dr. Olsavik specializes in injury rehab and sports medicine. She is highly trained having received her MD and Residency in Physiatry from Pellham Institute. Her passion is to help injured people get back to their life.
[portrait here]
Wendy Carstairs, PT
Physiotherapist
Wendy has over 10 years of experience as a Physiotherapist (5 in Canada). She has advanced training in orthopedics and manual therapy. She loves and relates well with people from the youngest to the most senior.
--------------------[location: inside, middle panel]-------------------------------
Our services
We provide integrated assessment and care from interprofessional team of regulated healthcare professionals with proven experience in injury rehabilitation:
physiatrists
sport medicine physicians
physiotherapists
chiropractors
massage therapists
acupuncturists
psychologists
We provide custom medical bracing, orthotics, orthopedic shoes, assistive devices, and medical stockings, all in one place.
----------------------[location: inside, right panel]-----------------------------------
Only registered physiotherapists
We strongly believe in consistency with your treatment plan. This means that you spend your time here one-on-one with your physiotherapist, not any students or assistants. You get consistent high quality care from a professional.
One-on-one attention
We book maximum 3 people per hour to ensure everyone gets adequate one-on-one time with their physiotherapist. This compares favorably with other clinics, who may book upwards of 5-6 per hour. The atmosphere is professional -balanced with friendly, caring and relaxed. Our highly qualified staff operate this way to help make your recovery faster and more enjoyable.
------------------------[location: outside, left panel]---------------------------------
The right rehab for your clients
Timely access to comprehensive assessment and treatment
Proven track record in injury rehabilitation
Convenient one-stop service
Customized treatment plans
Integrated, co-ordinated care
Evidence-based care applying leading best practices
Access to specialty clinics: Physiatry and Chronic Pain
-------------------------[location: outside, middle panel]--------------------------
Please call us 555-384-2096
for more information on injury rehabilitation
Vela Mend Group
1862 Wexmoor Rd., Unit 9
Scarborough, ON K4T 8B2
[Please include a line art map designed based on "map" file enclosed]
To make a referral for your clients, contact velamendgroup@corvamail.ca or fax: 555-384-2071. Thank you.
www.velamendgroup.ca
------------------------------------------------------------------------------------------------
Target Market(s)
family doctors, ER docs, lawyers, and general public age (20-50)
Industry/Entity Type
Health And Wellness
Requirements
Must have
- san serif font
- blue and green colors
- clean, sophisticated look
Nice to have
- consumer choice award badge either on front or back of trifold
- see above

```html
<!DOCTYPE html>
<html lang="en">
<head>
<meta charset="utf-8">
<title>Vela Mend – Integrated Injury Rehab</title>
<link href="https://fonts.googleapis.com/css2?family=Fira+Sans:ital,wght@0,300;0,400;0,500;0,600;1,300;1,400&display=swap" rel="stylesheet">
<style>
  :root {
    --navy: #2c4f80;
    --navy-deep: #284a7a;
    --navy-light: #5a84b6;
    --green: #9cc53d;
    --green-text: #a9d043;
    --panel-grey: #eaebed;
    --swoosh-grey: #d9dbde;
    --body-grey: #4b4f55;
    --white: #ffffff;
    --photo-light: #e6e3df;
    --photo-mid: #c9b6a6;
    --portrait-tone: #b9a79a;
    --seal: #2c4f80;
  }
  * { margin: 0; padding: 0; box-sizing: border-box; }
  html, body { width: 1200px; height: 931px; overflow: hidden; background: var(--white); }
  .flyer-panel {
    position: relative; width: 1200px; height: 931px; overflow: hidden;
    font-family: "Fira Sans", sans-serif; background: var(--white);
  }
  .backdrop { position: absolute; inset: 0; }
  .hero-photo { position: absolute; left: 0; top: 0; width: 800px; height: 540px; }

  .feature { position: absolute; top: 24px; }
  .feature h2 { font-size: 19px; font-weight: 500; color: var(--navy); margin-bottom: 8px; white-space: nowrap; letter-spacing: -0.2px; }
  .feature p { font-size: 14px; line-height: 22.2px; color: var(--body-grey); text-align: justify; letter-spacing: -0.15px; }
  .feature--registered { left: 460px; width: 296px; }
  .feature--attention { left: 835px; width: 320px; }

  .brand { position: absolute; left: 25px; top: 262px; }
  .brand-name {
    display: flex; align-items: center; gap: 6px;
    font-size: 22px; font-weight: 600; color: var(--navy-light); line-height: 1; white-space: nowrap;
  }
  .brand-name .brand-dot { width: 11px; height: 11px; border-radius: 50%; background: var(--navy-light); }
  .brand-tagline { margin-top: 10px; font-size: 8px; font-weight: 500; color: var(--navy); border-top: 4px solid var(--navy-light); padding-top: 5px; white-space: nowrap; width: 82px; }

  .services { position: absolute; left: 838px; top: 302px; width: 317px; color: var(--navy); }
  .services h2 { font-size: 31px; font-weight: 300; margin-bottom: 6px; }
  .services p { font-size: 14.6px; line-height: 22.5px; text-align: justify; hyphens: auto; -webkit-hyphens: auto; }
  .service-list { list-style: none; position: absolute; left: 912px; top: 446px; }
  .service-list li {
    display: flex; align-items: center; gap: 6px; height: 30px;
    font-size: 15px; font-weight: 500; color: var(--navy);
  }
  .service-list svg { width: 18px; height: 18px; }

  .bracing-note {
    position: absolute; left: 888px; top: 701px; width: 272px;
    font-size: 14.6px; font-weight: 500; line-height: 22.5px; color: var(--white);
    text-align: right;
  }

  .award-seal { position: absolute; left: 1080px; top: 830px; width: 72px; height: 72px; }

  .profile { position: absolute; top: 558px; display: flex; gap: 14px; color: var(--white); }
  .profile--physiatrist { left: 23px; }
  .profile--physio { left: 418px; }
  .portrait { width: 122px; height: 170px; margin-top: 2px; }
  .profile-name { font-size: 16px; font-weight: 500; color: var(--green-text); line-height: 20px; }
  .profile-creds { font-size: 13px; color: var(--white); font-weight: 300; }
  .profile-role { font-size: 14.5px; font-weight: 300; font-style: italic; color: var(--green-text); line-height: 20px; margin-bottom: 6px; }
  .profile-bio { font-size: 14.6px; font-weight: 300; line-height: 22.2px; width: 222px; letter-spacing: -0.1px; }
</style>
</head>
<body>
<main class="flyer-panel">

  <svg class="backdrop" width="1200" height="931" viewBox="0 0 1200 931" aria-hidden="true">
    <defs>
      <linearGradient id="lowerBand" x1="0" y1="0" x2="1" y2="1">
        <stop offset="0" stop-color="#2f5688"/>
        <stop offset="1" stop-color="#6b93c2"/>
      </linearGradient>
    </defs>
    <path d="M445,0 C430,70 480,150 600,205 C700,245 785,272 865,270 C985,267 1100,242 1200,236 L1200,0 Z" fill="var(--panel-grey)"/>
    <path d="M895,640 C960,668 1090,684 1200,672 L1200,835 C1110,805 1010,798 935,835 C895,800 880,740 895,640 Z" fill="var(--green)"/>
    <path d="M935,835 C1010,798 1110,805 1200,835 L1200,931 L965,931 C955,895 945,860 935,835 Z" fill="var(--swoosh-grey)"/>
    <path d="M0,478 C150,468 300,522 450,517 C600,512 700,494 790,508 C875,525 892,610 890,690 C888,760 878,800 868,815 L0,815 Z" fill="var(--navy-deep)"/>
    <path d="M0,812 C150,860 320,880 520,850 C680,826 790,800 868,800 L960,931 L0,931 Z" fill="url(#lowerBand)"/>
    <path d="M0,812 C150,860 320,880 520,850 C680,826 790,800 868,800" fill="none" stroke="var(--green)" stroke-width="2.5"/>
  </svg>

  <svg class="hero-photo" viewBox="0 0 800 540" role="img" aria-label="Photo: physiotherapist's hands adjusting a hinged knee brace on a patient's leg">
    <defs>
      <linearGradient id="heroTone" x1="0" y1="0" x2="1" y2="1">
        <stop offset="0" stop-color="var(--photo-light)"/>
        <stop offset="0.55" stop-color="var(--photo-mid)"/>
        <stop offset="1" stop-color="#a9b8cc"/>
      </linearGradient>
    </defs>
    <path d="M0,0 L445,0 C430,70 480,150 600,205 C700,245 785,272 800,272 L800,508 C700,494 600,512 450,517 C300,522 150,468 0,478 Z" fill="url(#heroTone)"/>
    <path d="M0,180 C200,190 450,210 600,230 C720,248 790,272 800,272" fill="none" stroke="var(--navy)" stroke-width="2.5"/>
    <path d="M0,192 C200,202 440,222 590,242 C700,258 780,278 800,279" fill="none" stroke="var(--green)" stroke-width="2"/>
  </svg>
  <svg class="backdrop" width="1200" height="931" viewBox="0 0 1200 931" aria-hidden="true">
    <path d="M800,272 C840,272 855,271 865,270 C985,267 1100,242 1200,236" fill="none" stroke="var(--navy)" stroke-width="2.5"/>
    <path d="M800,279 C900,282 1040,262 1200,244" fill="none" stroke="var(--green)" stroke-width="2"/>
  </svg>

  <section class="feature feature--registered">
    <h2>Only registered physiotherapists</h2>
    <p>We strongly believe in consistency with your treatment plan. This means that you spend your time here one-on-one with your physiotherapist, not any students or assistants. You get consistent high quality care from a professional.</p>
  </section>

  <section class="feature feature--attention">
    <h2>One-on-one attention</h2>
    <p>We book maximum 3 people per hour to ensure everyone gets adequate one-on-one time with their physiotherapist. This compares favorably with other clinics, who may book upwards of 5-6 per hour. The atmosphere is professional - balanced with friendly, caring and relaxed. Our highly qualified staff operate this way to help make your recovery faster and more enjoyable.</p>
  </section>

  <div class="brand">
    <div class="brand-name"><span>Vela Mend</span><span class="brand-dot"></span></div>
    <div class="brand-tagline">Integrated Injury Rehab</div>
  </div>

  <section class="services">
    <h2>Our services</h2>
    <p>We provide integrated assessment and care from interprofessional team of regulated healthcare professionals with proven experience in injury rehabilitation:</p>
  </section>

  <ul class="service-list">
    <li><svg viewBox="0 0 18 18" aria-hidden="true"><circle cx="8" cy="10" r="6.5" fill="none" stroke="var(--green)" stroke-width="1.5"/><path d="M4.5,9.5 L7.5,12.5 L15,3" fill="none" stroke="var(--green)" stroke-width="2"/></svg>physiatrists</li>
    <li><svg viewBox="0 0 18 18" aria-hidden="true"><circle cx="8" cy="10" r="6.5" fill="none" stroke="var(--green)" stroke-width="1.5"/><path d="M4.5,9.5 L7.5,12.5 L15,3" fill="none" stroke="var(--green)" stroke-width="2"/></svg>sport medicine physicians</li>
    <li><svg viewBox="0 0 18 18" aria-hidden="true"><circle cx="8" cy="10" r="6.5" fill="none" stroke="var(--green)" stroke-width="1.5"/><path d="M4.5,9.5 L7.5,12.5 L15,3" fill="none" stroke="var(--green)" stroke-width="2"/></svg>physiotherapists</li>
    <li><svg viewBox="0 0 18 18" aria-hidden="true"><circle cx="8" cy="10" r="6.5" fill="none" stroke="var(--green)" stroke-width="1.5"/><path d="M4.5,9.5 L7.5,12.5 L15,3" fill="none" stroke="var(--green)" stroke-width="2"/></svg>chiropractors</li>
    <li><svg viewBox="0 0 18 18" aria-hidden="true"><circle cx="8" cy="10" r="6.5" fill="none" stroke="var(--green)" stroke-width="1.5"/><path d="M4.5,9.5 L7.5,12.5 L15,3" fill="none" stroke="var(--green)" stroke-width="2"/></svg>massage therapists</li>
    <li><svg viewBox="0 0 18 18" aria-hidden="true"><circle cx="8" cy="10" r="6.5" fill="none" stroke="var(--green)" stroke-width="1.5"/><path d="M4.5,9.5 L7.5,12.5 L15,3" fill="none" stroke="var(--green)" stroke-width="2"/></svg>acupuncturists</li>
    <li><svg viewBox="0 0 18 18" aria-hidden="true"><circle cx="8" cy="10" r="6.5" fill="none" stroke="var(--green)" stroke-width="1.5"/><path d="M4.5,9.5 L7.5,12.5 L15,3" fill="none" stroke="var(--green)" stroke-width="2"/></svg>psychologists</li>
  </ul>

  <p class="bracing-note">We provide custom medical bracing, orthotics, orthopedic shoes, assistive devices, and medical stockings, all in one place.</p>

  <svg class="award-seal" viewBox="0 0 72 72" role="img" aria-label="Consumer award badge">
    <circle cx="36" cy="36" r="32" fill="var(--seal)"/>
  </svg>

  <article class="profile profile--physiatrist">
    <svg class="portrait" viewBox="0 0 122 170" role="img" aria-label="Portrait of Dr. Harriet Olsavik, physiatrist">
      <rect width="122" height="170" fill="var(--portrait-tone)"/>
    </svg>
    <div>
      <h3 class="profile-name">Harriet Olsavik,</h3>
      <div class="profile-creds">MD, FRCPC, MSC, CIME</div>
      <div class="profile-role">Physiatrist</div>
      <p class="profile-bio">Dr. Olsavik specializes in injury rehab and sports medicine. She is highly trained having received her MD and Residency in Physiatry from Pellham Institute. Her passion is to help injured people get back to their life.</p>
    </div>
  </article>

  <article class="profile profile--physio">
    <svg class="portrait" viewBox="0 0 122 170" role="img" aria-label="Portrait of Wendy Carstairs, physiotherapist">
      <rect width="122" height="170" fill="#c8c3bd"/>
    </svg>
    <div>
      <h3 class="profile-name">Wendy Carstairs, <span class="profile-creds">PT</span></h3>
      <div class="profile-role">Physiotherapist</div>
      <p class="profile-bio">Wendy has over 10 years of experience as a Physiotherapist (5 in Canada). She has advanced training in orthopedics and manual therapy. She loves and relates well with people form the youngest to the most senior.</p>
    </div>
  </article>

</main>
</body>
</html>
```